Vantiqo custom business card design

Need a authentic, innovative business card design for a new mobile app business. I am uploading a few screen images from our app for you to view. I would like app design theme to match business card design. I can also send logo images.

```html
<!DOCTYPE html>
<html lang="en">
<head>
<meta charset="utf-8">
<title>Vantiqo business card</title>
<link rel="stylesheet" href="https://fonts.googleapis.com/css2?family=Montserrat:wght@700;800&family=Open+Sans:wght@400;600&display=swap">
<style>
  :root {
    --page-bg: #8c8c8c;
    --card-light: #efefef;
    --card-dark: #1c1c1c;
    --card-dark-glow: #3a3a3a;
    --brand-purple: #5e0a8e;
    --ink: #1d1d1d;
    --rule: #a9a9a9;
    --white: #f2f2f2;
  }
  html, body {
    margin: 0;
    padding: 0;
    width: 1200px;
    height: 1200px;
    overflow: hidden;
    background: var(--page-bg);
  }
  .canvas {
    position: relative;
    width: 1200px;
    height: 1200px;
  }
  .card {
    position: absolute;
    top: 310px;
    width: 366px;
    height: 594px;
    box-shadow: 0 3px 8px rgba(0,0,0,0.35);
  }
  .card--front {
    left: 233px;
    background: var(--card-light);
    color: var(--ink);
    font-family: "Open Sans", Arial, sans-serif;
    text-align: center;
  }
  .card--back {
    left: 628px;
    width: 370px;
    background: radial-gradient(circle at 60% 20%, var(--card-dark-glow) 0%, var(--card-dark) 60%);
    text-align: center;
  }
  .brand-mark {
    position: absolute;
    left: 0;
    right: 0;
    display: flex;
    flex-direction: column;
    align-items: center;
  }
  .card--front .brand-mark { top: 92px; }
  .card--back .brand-mark { top: 185px; }
  .brand-dot {
    border-radius: 50%;
    background: var(--brand-purple);
  }
  .card--front .brand-dot { width: 78px; height: 78px; margin-bottom: 22px; }
  .card--back .brand-dot { width: 110px; height: 110px; margin-bottom: 40px; }
  .brand-name {
    font-family: "Montserrat", Arial, sans-serif;
    font-weight: 800;
    letter-spacing: 0.5px;
    line-height: 1;
  }
  .card--front .brand-name { font-size: 44px; color: var(--ink); }
  .card--back .brand-name { font-size: 62px; color: var(--white); }
  .person {
    position: absolute;
    top: 344px;
    left: 0;
    right: 0;
  }
  .person__name {
    margin: 0;
    font-family: "Montserrat", Arial, sans-serif;
    font-weight: 700;
    font-size: 24px;
    color: var(--brand-purple);
    line-height: 1.1;
  }
  .person__role {
    margin: 2px 0 0;
    font-size: 17px;
    line-height: 1.2;
  }
  .rule {
    position: absolute;
    left: 86px;
    width: 200px;
    height: 1px;
    background: var(--rule);
    border: 0;
    margin: 0;
  }
  .rule--top { top: 397px; }
  .rule--bottom { top: 508px; }
  .contact {
    position: absolute;
    top: 406px;
    left: 0;
    right: 0;
    margin: 0;
    padding: 0;
    list-style: none;
    font-size: 17.5px;
    line-height: 21.5px;
  }
  .contact__label { color: var(--brand-purple); }
  .contact__web { color: var(--brand-purple); font-weight: 600; }
  .address {
    position: absolute;
    top: 514px;
    left: 0;
    right: 0;
    margin: 0;
    font-style: normal;
    font-size: 17.5px;
    line-height: 21.5px;
  }
</style>
</head>
<body>
<main class="canvas">
  <section class="card card--front" aria-label="Card front">
    <div class="brand-mark">
      <span class="brand-dot"></span>
      <span class="brand-name">Vantiqo</span>
    </div>
    <div class="person">
      <h1 class="person__name">MARCUS HALE</h1>
      <p class="person__role">Managing Director</p>
    </div>
    <hr class="rule rule--top">
    <ul class="contact">
      <li><span class="contact__label">P:</span> 051-274 380 612</li>
      <li><span class="contact__label">M:</span> 051-274 380 619</li>
      <li><span class="contact__label">E:</span> info@vantiqomail.com</li>
      <li class="contact__web">www.vantiqoapp.com</li>
    </ul>
    <hr class="rule rule--bottom">
    <address class="address">48 Larkspur Lane, Suite 9<br>Northvale, 204518.</address>
  </section>

  <section class="card card--back" aria-label="Card back">
    <div class="brand-mark">
      <span class="brand-dot"></span>
      <span class="brand-name">Vantiqo</span>
    </div>
  </section>
</main>
</body>
</html>
```